New Interrior Decoration company needs new website

We need a website for our new company specialising in interior decoration to residential and commercial markets.
We supply and install decorative and printed films for office and home decoration such as feature walls.
We would like to keep the design simple and clean.

Target Market(s)

Architects and interior designaers

Industry/Entity Type

It Company

Number of Pages Required

5+ page

Font styles to use
Sans Serif

Requirements
Must have
• Home page,
• Services/products page (split into commercial and residential)
• Gallery (split into commercial and residential)
• contact form and page
Nice to have
• Very clean and minimalistic design.

```html
<!DOCTYPE html>
<html lang="en">
<head>
<meta charset="utf-8">
<title>Vela Interiors</title>
<link href="https://fonts.googleapis.com/css2?family=Raleway:wght@400;500;700&family=Open+Sans:wght@400;600;700&display=swap" rel="stylesheet">
<style>
:root{
  --blue:#0a5cb8;
  --ink:#333333;
  --text:#666666;
  --light:#f3f3f3;
  --white:#ffffff;
  --footer:#3b3b3b;
  --footer-box:#555555;
  --footer-line:#4c4c4c;
}
*{margin:0;padding:0;box-sizing:border-box}
html,body{width:998px;height:1200px;overflow:hidden;background:var(--white)}
body{position:relative;font-family:'Open Sans',sans-serif;color:var(--text)}
.site-header{position:absolute;top:0;left:0;width:998px;height:87px;background:var(--white)}
.brand{position:absolute;left:64px;top:20px;display:flex;align-items:center;gap:10px}
.brand-square{width:40px;height:40px;background:var(--blue)}
.brand-name{font-family:'Raleway',sans-serif;font-weight:700;font-size:28px;color:var(--ink);letter-spacing:.5px}
.main-nav{position:absolute;top:26px;left:406px;display:flex}
.main-nav a{font-family:'Raleway',sans-serif;font-size:17px;color:var(--ink);text-decoration:none;height:39px;line-height:39px;padding:0 17px;margin-right:3px}
.main-nav a.active{background:var(--blue);color:var(--white)}
.main-nav a.spaced{margin-right:10px}
.hero{position:absolute;top:87px;left:0;width:998px;height:477px;background:linear-gradient(160deg,#8c857d 0%,#c9c5c0 40%,#a6a7a4 65%,#6a6864 100%)}
.markets{position:absolute;top:564px;left:0;width:998px;height:234px;background:var(--light)}
.market{position:absolute;top:-52px;width:290px;text-align:center}
.market-icon{width:104px;height:104px;border-radius:50%;background:var(--blue);margin:0 auto;display:flex;align-items:center;justify-content:center}
.market h2{font-family:'Raleway',sans-serif;font-weight:400;font-size:22px;color:var(--ink);margin-top:13px}
.market p{font-size:13px;line-height:21px;margin-top:8px}
.read-more{font-family:'Raleway',sans-serif;font-size:16px;color:var(--blue);text-decoration:none;display:inline-block;margin-top:3px}
.welcome{position:absolute;top:830px;left:0;width:998px;text-align:center}
.welcome h1{font-family:'Raleway',sans-serif;font-weight:400;font-size:36px;color:var(--ink)}
.welcome h1 span{color:var(--blue)}
.welcome p{width:720px;margin:18px auto 0;font-size:13.5px;line-height:21px}
.btn{display:inline-block;margin-top:14px;background:var(--blue);color:var(--white);font-family:'Raleway',sans-serif;font-size:16px;padding:0 22px;height:43px;line-height:43px;border-radius:2px;text-decoration:none}
.site-footer{position:absolute;top:1054px;left:0;width:998px;height:146px;background:var(--footer);color:var(--white)}
.contact-item{position:absolute;top:28px;display:flex;align-items:flex-start;gap:12px}
.contact-icon{width:43px;height:43px;background:var(--footer-box);border-radius:2px;display:flex;align-items:center;justify-content:center;flex:none}
.contact-item span{font-size:14px;line-height:21px}
.contact-item .phone{font-weight:700;font-size:19px;line-height:43px}
.footer-rule{position:absolute;top:96px;left:64px;width:871px;border-top:1px solid var(--footer-line)}
.copyright{position:absolute;top:114px;width:998px;text-align:center;font-size:13px}
</style>
</head>
<body>
<header class="site-header">
  <div class="brand"><div class="brand-square"></div><span class="brand-name">VELA INTERIORS</span></div>
  <nav class="main-nav">
    <a class="active" href="#">HOME</a><a href="#">ABOUT</a><a class="spaced" href="#">SERVICES</a><a class="spaced" href="#">GALLERY</a><a href="#">CONTACT</a>
  </nav>
</header>

<div class="hero" role="img" aria-label="Photo of a modern open-plan kitchen and dining room with pendant lamps"></div>

<section class="markets">
  <div class="market" style="left:166px">
    <div class="market-icon">
      <svg width="46" height="40" viewBox="0 0 46 40"><path d="M23 2 L2 20 H8 V38 H19 V27 H27 V38 H38 V20 H44 Z" fill="#fff"/><rect x="33" y="5" width="5" height="10" fill="#fff"/></svg>
    </div>
    <h2>Residential Interiors</h2>
    <p>Lorem Ipsum is simply dummy text of the printing and typesetting industry. Lorem Ipsum has been the industry.</p>
    <a class="read-more" href="#">READ MORE &#187;</a>
  </div>
  <div class="market" style="left:533px">
    <div class="market-icon">
      <svg width="54" height="48" viewBox="0 0 54 48" fill="#fff"><path d="M18 46 V10 L32 2 V46 Z"/><rect x="2" y="20" width="14" height="26"/><rect x="34" y="24" width="18" height="22"/><g fill="#0a5cb8"><rect x="5" y="24" width="3" height="3"/><rect x="10" y="24" width="3" height="3"/><rect x="5" y="31" width="3" height="3"/><rect x="10" y="31" width="3" height="3"/><rect x="5" y="38" width="3" height="3"/><rect x="10" y="38" width="3" height="3"/><rect x="38" y="29" width="4" height="3"/><rect x="45" y="29" width="4" height="3"/><rect x="38" y="36" width="4" height="3"/><rect x="45" y="36" width="4" height="3"/></g></svg>
    </div>
    <h2>Commercial Interiors</h2>
    <p>Lorem Ipsum is simply dummy text of the printing and typesetting industry. Lorem Ipsum has been the industry.</p>
    <a class="read-more" href="#">READ MORE &#187;</a>
  </div>
</section>

<section class="welcome">
  <h1>WELCOME TO <span>VELA INTERIORS</span></h1>
  <p>Lorem Ipsum is simply dummy text of the printing and typesetting industry. Lorem Ipsum has been the industry's standard dummy text ever since the 1500s, when an unknown printer took a galley of type and scrambled it to make a type specimen book.</p>
  <a class="btn" href="#">READ MORE</a>
</section>

<footer class="site-footer">
  <div class="contact-item" style="left:64px">
    <div class="contact-icon"><svg width="14" height="20" viewBox="0 0 14 20"><path d="M7 0 A7 7 0 0 0 0 7 C0 12 7 20 7 20 C7 20 14 12 14 7 A7 7 0 0 0 7 0 Z" fill="#fff"/><circle cx="7" cy="7" r="2.5" fill="#555"/></svg></div>
    <span>Lorem Ipsum is dummy<br>text of the printing.</span>
  </div>
  <div class="contact-item" style="left:365px">
    <div class="contact-icon"><svg width="20" height="20" viewBox="0 0 20 20"><path d="M4 1 L8 5 L6 8 C7 11 9 13 12 14 L15 12 L19 16 L16 19 C8 18 2 12 1 4 Z" fill="#fff"/></svg></div>
    <span class="phone">123 456 7890</span>
  </div>
  <div class="contact-item" style="left:665px">
    <div class="contact-icon"><svg width="20" height="15" viewBox="0 0 20 15"><rect x="1" y="1" width="18" height="13" rx="2" fill="none" stroke="#fff" stroke-width="1.8"/><path d="M1.5 2.5 L10 9 L18.5 2.5" fill="none" stroke="#fff" stroke-width="1.8"/></svg></div>
    <span>info@velainteriors.com</span>
  </div>
  <div class="footer-rule"></div>
  <p class="copyright">&copy; <strong>VELA INTERIORS</strong> - 2016. All Rights Reserved.</p>
</footer>
</body>
</html>
```